Dunmore Roofing

Want a professional looking business card

Industry/Entity Type

Business

Contact Information for Business Card

Paul Dunmore ( Owner) paul@dunmoreroofing-example.com, www.dunmoreroofing-example.com, Adress: 4172 Township road 43 Ashcombe Falls,WR K9X4T2

```html
<!DOCTYPE html>
<html lang="en">
<head>
<meta charset="utf-8">
<title>Dunmore Roofing – Business Card</title>
<link rel="stylesheet" href="https://fonts.googleapis.com/css2?family=Open+Sans:wght@400;600;700&display=swap">
<style>
  :root {
    --page: #d9dadc;
    --brand-blue: #1c4788;
    --card-grey: #77787b;
    --divider-grey: #8a8b8e;
    --pale-grey: #e3e4e6;
    --window-grey: #d4d5d7;
    --white: #ffffff;
    --icon-grey: #9a9ca0;
  }
  * { box-sizing: border-box; margin: 0; padding: 0; }
  html, body {
    width: 1200px; height: 900px; overflow: hidden;
    background: var(--page);
    font-family: "Open Sans", Arial, sans-serif;
  }
  .canvas { position: relative; width: 1200px; height: 900px; }

  .card {
    position: absolute; width: 600px; height: 343px; overflow: hidden;
    box-shadow: 0 6px 18px rgba(0,0,0,.18);
  }
  .card svg.card-art { position: absolute; inset: 0; }

  /* Back card */
  .card--back { left: 60px; top: 80px; background: var(--card-grey); }
  .back-map {
    position: absolute; left: 150px; top: 50px; width: 300px; height: 200px;
    background: radial-gradient(ellipse at center, rgba(255,255,255,.08), rgba(255,255,255,0) 70%);
  }
  .back-name {
    position: absolute; left: 0; right: 0; top: 112px; text-align: center;
    color: var(--white); font-weight: 700; line-height: 1;
  }
  .back-name .line-main { display: block; font-size: 50px; letter-spacing: 2px; }
  .back-name .line-sub { display: block; font-size: 18px; letter-spacing: 16px; margin-top: 10px; padding-left: 16px; }
  .back-web {
    position: absolute; left: 0; right: 0; top: 272px;
    display: flex; align-items: center; justify-content: center; gap: 12px;
    color: var(--white); font-size: 13px; line-height: 1;
  }
  .back-web .rule { width: 80px; height: 1px; background: rgba(255,255,255,.6); }

  /* Front card */
  .card--front { left: 540px; top: 480px; background: var(--white); }
  .front-name {
    position: absolute; left: 36px; top: 74px; color: var(--brand-blue);
    font-weight: 700; line-height: 1; display: flex; align-items: flex-start; gap: 10px;
  }
  .front-name .mark-square { width: 14px; height: 14px; background: var(--brand-blue); margin-top: 8px; }
  .front-name .line-main { display: block; font-size: 40px; letter-spacing: 1px; }
  .front-name .line-sub { display: block; font-size: 15px; letter-spacing: 14px; margin-top: 8px; }

  .contact-list {
    position: absolute; left: 22px; top: 220px; list-style: none; color: var(--white);
    font-size: 14px;
  }
  .contact-list li { display: flex; align-items: center; gap: 10px; height: 26px; }
  .contact-icon { width: 18px; height: 18px; flex: none; }

  .owner {
    position: absolute; right: 22px; top: 150px; text-align: right; color: var(--white);
  }
  .owner .person { font-size: 21px; font-weight: 700; line-height: 1.15; }
  .owner .role { font-size: 14px; line-height: 1.3; }

  .address {
    position: absolute; right: 22px; top: 246px; text-align: right; color: var(--white);
    font-size: 13px; line-height: 1.45; font-style: normal;
  }
  .address .company { font-weight: 700; }
</style>
</head>
<body>
<main class="canvas">

  <section class="card card--back" aria-label="Business card back">
    <div class="back-map" role="img" aria-label="Faint dotted world map pattern"></div>
    <h1 class="back-name"><span class="line-main">DUNMORE</span><span class="line-sub">ROOFING</span></h1>
    <p class="back-web"><span class="rule"></span>www.dunmoreroofing-example.com<span class="rule"></span></p>
  </section>

  <section class="card card--front" aria-label="Business card front">
    <svg class="card-art" width="600" height="343" viewBox="0 0 600 343" aria-hidden="true">
      <polygon points="300,0 600,0 600,7 295,7" fill="var(--brand-blue)"/>
      <polygon points="280,7 600,7 600,10 282,10" fill="var(--divider-grey)"/>
      <polygon points="455,10 478,10 470,130 447,130" fill="var(--pale-grey)"/>
      <rect x="510" y="38" width="24" height="24" fill="var(--window-grey)"/>
      <rect x="538" y="38" width="24" height="24" fill="var(--window-grey)"/>
      <rect x="510" y="66" width="24" height="24" fill="var(--window-grey)"/>
      <rect x="538" y="66" width="24" height="24" fill="var(--window-grey)"/>
      <rect x="0" y="200" width="332" height="5" fill="var(--divider-grey)"/>
      <rect x="0" y="205" width="328" height="138" fill="var(--brand-blue)"/>
      <rect x="328" y="130" width="272" height="5" fill="var(--divider-grey)"/>
      <rect x="328" y="135" width="6" height="208" fill="var(--divider-grey)"/>
      <rect x="334" y="135" width="266" height="208" fill="var(--brand-blue)"/>
      <rect x="334" y="228" width="266" height="3" fill="var(--divider-grey)"/>
    </svg>

    <h2 class="front-name"><span class="mark-square"></span><span><span class="line-main">DUNMORE</span><span class="line-sub">ROOFING</span></span></h2>

    <ul class="contact-list">
      <li>
        <svg class="contact-icon" viewBox="0 0 18 18" aria-hidden="true"><circle cx="9" cy="9" r="9" fill="var(--icon-grey)"/><path d="M6 4.5l2 2-1 1.2c.6 1.4 1.7 2.5 3.1 3.1l1.2-1 2 2-1.2 1.5C9 13 5 9 4.7 5.7z" fill="var(--white)"/></svg>
        (555) 555-0147
      </li>
      <li>
        <svg class="contact-icon" viewBox="0 0 18 18" aria-hidden="true"><circle cx="9" cy="9" r="9" fill="var(--icon-grey)"/><rect x="4.5" y="6" width="9" height="6.5" fill="var(--white)"/><path d="M4.5 6l4.5 3.5L13.5 6" stroke="var(--icon-grey)" stroke-width="1" fill="none"/></svg>
        paul@dunmoreroofing-example.com
      </li>
      <li>
        <svg class="contact-icon" viewBox="0 0 18 18" aria-hidden="true"><circle cx="9" cy="9" r="9" fill="var(--icon-grey)"/><circle cx="9" cy="9" r="4.5" stroke="var(--white)" stroke-width="1" fill="none"/><ellipse cx="9" cy="9" rx="2" ry="4.5" stroke="var(--white)" stroke-width="1" fill="none"/><line x1="4.5" y1="9" x2="13.5" y2="9" stroke="var(--white)" stroke-width="1"/></svg>
        www.dunmoreroofing-example.com
      </li>
    </ul>

    <div class="owner">
      <p class="person">Paul Dunmore</p>
      <p class="role">Owner</p>
    </div>

    <address class="address">
      <p class="company">Dunmore Roofing</p>
      <p>4172 Township road 43,</p>
      <p>Ashcombe Falls,WR K9X4T2</p>
    </address>
  </section>

</main>
</body>
</html>
```